Willow Cradle Pregnancy and Baby Massage

I need a web design for a new business, WILLOW CRADLE PREGNANCY AND BABY MASSAGE that I am in the process of setting up in the suburbs of Perth, Western Australia. The business is owned and operated by myself and my intention is to service Pregnant Mothers and Parents of Young Babies that would benefit from massage. I would like to have a "Home Page" and pages for "About Me", "Pregnancy Massage", "Baby Massage", a Pricing Page for Pregnancy Massage Sessions, a Pricing Page for Baby Massage Sessions, and a "Contact Me" page to allow clients to either contact me with queries or book available pregnancy massage sessions on a particular day of the week. I would also like a "News" page that would include articles I have written, news about new courses and a link to my Facebook page (yet to be set up). I would like to keep the colour schemes similar to my logo design colours. I need the design to be easy to follow and to appeal to a younger audience (20's to mid 30's).
The target audience is pregnant mothers-to-be wishing to receive massage treatments, and new parents and grandparents of small babies that would like to learn how to massage their babies.
The look and feel should be modern, professional, elegant and feminine.
I need the design to be in a standard format such that I can update the content by myself ( and does not need specialised software) as the company and business progresses.

Target Market(s)

Contact Information for Business Card

Card should have rounded edges. Design should have the same "feel" as the website. Contact Details of my business address, mobile phone, email and website should be included.

Font styles to use
Script

Requirements
Must have
• Same colours as logo design. In cmyk system, the colours are: 20,60,0,0 which best result is pantone 681 and 40,40,0,0 which best result is pantone 2645. Card should include the logo design.

```html
<!DOCTYPE html>
<html lang="en">
<head>
<meta charset="utf-8">
<title>Willow Cradle Pregnancy and Baby Massage</title>
<link href="https://fonts.googleapis.com/css2?family=Mulish:wght@400;600&family=Open+Sans:wght@400&display=swap" rel="stylesheet">
<style>
  :root {
    --plum: #a65b9a;
    --plum-dark: #94488a;
    --lavender: #8d86c1;
    --pink-band: #c070ab;
    --text-grey: #777777;
    --footer-bg: #f1f1f1;
    --footer-line: #e2e2e2;
    --white: #ffffff;
  }
  * { box-sizing: border-box; margin: 0; padding: 0; }
  html, body { width: 978px; height: 1200px; overflow: hidden; background: var(--white); }
  body { position: relative; font-family: "Mulish", sans-serif; }

  .site-header { position: absolute; top: 0; left: 0; width: 978px; height: 91px; display: flex; align-items: center; justify-content: center; gap: 10px; }
  .brand-dot { width: 34px; height: 34px; border-radius: 50%; background: var(--plum); }
  .brand-name { font-family: "Mulish", sans-serif; font-weight: 600; font-size: 19px; color: var(--plum); }

  .main-nav { position: absolute; top: 91px; left: 0; width: 978px; height: 42px; background: linear-gradient(180deg, #c27ab4 0%, #a95799 100%); }
  .main-nav ul { list-style: none; display: flex; position: absolute; left: 97px; top: 0; height: 42px; }
  .main-nav li { height: 42px; display: flex; align-items: center; padding: 0 18px; color: var(--white); font-size: 12.5px; letter-spacing: 0.2px; border-right: 1px solid rgba(255,255,255,0.35); }
  .main-nav li:last-child { border-right: none; }
  .main-nav li.active { background: linear-gradient(180deg, #a49fd3 0%, #8882c0 100%); padding: 0 27px; }

  .hero { position: absolute; top: 133px; left: 0; width: 978px; height: 527px; overflow: hidden; }
  .hero-photo { position: absolute; inset: 0; background: linear-gradient(100deg, #6e5250 0%, #8a6a68 35%, #c98a78 60%, #d9b9a4 85%, #b89a8a 100%); }
  .hero-copy { position: absolute; left: 91px; top: 133px; width: 400px; color: var(--white); }
  .hero-copy h1 { font-weight: 600; font-size: 30px; margin-bottom: 16px; }
  .hero-copy p { font-size: 16.5px; line-height: 24px; }
  .slider-dots { position: absolute; left: 456px; top: 396px; display: flex; gap: 7px; }
  .slider-dots span { width: 12px; height: 12px; border-radius: 50%; background: var(--white); }
  .slider-dots span.current { background: transparent; border: 2px solid var(--white); }
  .hero-wave { position: absolute; left: 0; top: 407px; }

  .vision-photo { position: absolute; left: 105px; top: 619px; width: 290px; height: 290px; border-radius: 50%; border: 3px solid var(--white); background: radial-gradient(circle at 50% 45%, #c9a08e 0%, #8b6a58 55%, #4f3e34 100%); box-shadow: 0 8px 22px rgba(0,0,0,0.22); }
  .vision { position: absolute; left: 418px; top: 638px; width: 455px; }
  .vision h2 { font-weight: 400; font-size: 29px; color: var(--lavender); margin-bottom: 14px; }
  .vision p { font-family: "Open Sans", sans-serif; font-size: 13px; line-height: 25px; color: var(--text-grey); }
  .read-more { position: absolute; left: 414px; top: 849px; width: 117px; height: 35px; background: linear-gradient(180deg, #b86aa9 0%, #9c4f8f 100%); color: var(--white); font-size: 14px; display: flex; align-items: center; justify-content: center; }
  .certification-badge { position: absolute; left: 404px; top: 930px; width: 220px; height: 122px; background: #f4ebf3; border-radius: 6px; }

  .site-footer { position: absolute; top: 1085px; left: 0; width: 978px; height: 115px; background: var(--footer-bg); border-top: 2px solid var(--footer-line); }
  .footer-nav { position: absolute; left: 104px; top: 40px; display: flex; gap: 24px; list-style: none; font-size: 13.5px; color: #555; }
  .copyright { position: absolute; left: 104px; top: 67px; font-size: 10.5px; color: #777; }
  .social { position: absolute; left: 751px; top: 38px; display: flex; gap: 4px; }
  .social span { width: 28px; height: 28px; border-radius: 50%; border: 1.5px solid var(--plum); }
</style>
</head>
<body>
  <header class="site-header">
    <span class="brand-dot"></span>
    <span class="brand-name">Willow Cradle Pregnancy and Baby Massage</span>
  </header>

  <nav class="main-nav">
    <ul>
      <li class="active">HOME</li>
      <li>ABOUT ME</li>
      <li>PREGNANCY MASSAGE</li>
      <li>BABY MASSAGE</li>
      <li>PRICING</li>
      <li>NEWS</li>
      <li>CONTACT US</li>
    </ul>
  </nav>

  <section class="hero">
    <div class="hero-photo" role="img" aria-label="Photo of two sleeping newborn twins wrapped in a coral blanket on a cream lace background"></div>
    <div class="hero-copy">
      <h1>Welcome to Our Website</h1>
      <p>Willow Cradle Pregnancy and Baby Massage was launched in 2017, offering massage for pregnant women, and instruction of baby massage to parents, grandparents and carers.</p>
    </div>
    <div class="slider-dots"><span class="current"></span><span></span><span></span><span></span></div>
    <svg class="hero-wave" width="978" height="120" viewBox="0 0 978 120" aria-hidden="true">
      <defs>
        <linearGradient id="waveBand" x1="0" x2="1" y1="0" y2="0">
          <stop offset="0" stop-color="#8d86c1"/>
          <stop offset="1" stop-color="#c070ab"/>
        </linearGradient>
      </defs>
      <path d="M0 80 C300 10 700 -8 978 56 L978 120 L0 120 Z" fill="url(#waveBand)"/>
      <path d="M0 112 C300 22 700 12 978 112 L978 120 L0 120 Z" fill="#ffffff"/>
    </svg>
  </section>

  <div class="vision-photo" role="img" aria-label="Round photo of two newborn babies cuddling on a soft fur blanket"></div>

  <section class="vision">
    <h2>Our Vision</h2>
    <p>My vision is to provide a professional massage service to pregnant mothers and babies that also benefitsfrom my skills and experience as a midwife.<br>
    My expectation is that after each session, my clients should leave feeling relaxed, calm,emotionally nurtured, soothed and supported.<br>
    At all times, I will take the utmost care of your privacy, safety and comfort in what is a very personal, intimate time in your life.</p>
  </section>
  <div class="read-more">Read More</div>

  <div class="certification-badge" role="img" aria-label="Certification badge"></div>

  <footer class="site-footer">
    <ul class="footer-nav">
      <li>Home</li>
      <li>About Me</li>
      <li>Pregnancy Massage</li>
      <li>Baby Massage</li>
      <li>Pricing</li>
      <li>News</li>
      <li>Contact Us</li>
    </ul>
    <p class="copyright">© 2017 Company Name &nbsp;All right reserved &nbsp;Term of Use</p>
    <div class="social" aria-label="Social links"><span></span><span></span><span></span><span></span></div>
  </footer>
</body>
</html>
```